TL - business card

Tallow Partners is an insurance brokerage firm, inovative, proactive, vigorous, which aims to become the leader of the insurance brokers in Anfrica. We should like to get some designs which should be avoided also in Gray / Metallic for the Administration and Orange / Blue for the Managers (ike in the picture sent). The Blue / Green logo is not the correct one, but the source of the file. Please adjust the color accordingly for the business cards. 1 / Orange / Blue 2 / Gray / Metallic We want something classic but which is transmitted strenght, inovation, modernity and most of all, rapidity. We want something start-up like, very punchy and catching eye remaining profesional at the same time. Name: Dorian Whitlock Function: Managing Director Address: N ° 17/18 Rua Veloso - R / C 2B Direita - Bairro Mutamba - Luanda Tel: (+244) 947 582 316 Email: dorian.whitlock@tallow-p.example Website: www.tallow-p. example We want classic in the front and creative, colorfull at the back. The cards will be printed in relief, with very high quality of paper.
Insurance Broker
Colors
Designer to choose colors to be used in the design.

```html
<!DOCTYPE html>
<html lang="en">
<head>
<meta charset="utf-8">
<title>Tallow Partners – business card</title>
<link rel="stylesheet" href="https://fonts.googleapis.com/css2?family=Exo+2:wght@600&family=Lato:wght@400&display=swap">
<style>
  :root {
    --backdrop: #2b2b2b;
    --paper: #ffffff;
    --brand-orange: #f0691f;
    --brand-blue: #29a6e0;
    --ink: #222222;
    --rule: #555555;
  }
  html, body {
    margin: 0;
    padding: 0;
    width: 1200px;
    height: 1200px;
    overflow: hidden;
    background: var(--backdrop);
  }
  .canvas {
    position: relative;
    width: 1200px;
    height: 1200px;
  }
  .card {
    position: absolute;
    top: 310px;
    height: 594px;
    box-shadow: 0 3px 8px rgba(0,0,0,0.45);
  }
  .card--front {
    left: 234px;
    width: 364px;
    background: var(--paper);
    font-family: "Lato", sans-serif;
    color: var(--ink);
    text-align: center;
  }
  .card--back {
    left: 627px;
    width: 369px;
    background: var(--brand-orange);
  }
  .brand-mark {
    position: absolute;
    left: 50%;
    top: 100px;
    width: 100px;
    height: 100px;
    margin-left: -50px;
  }
  .brand-name {
    position: absolute;
    left: 0;
    right: 0;
    font-family: "Exo 2", sans-serif;
    font-weight: 600;
    letter-spacing: 0.2px;
    margin: 0;
  }
  .card--front .brand-name {
    top: 201px;
    font-size: 27px;
    color: var(--brand-orange);
  }
  .card--back .brand-name {
    top: 506px;
    font-size: 29px;
    color: var(--paper);
  }
  .holder {
    position: absolute;
    left: 0;
    right: 0;
    top: 362px;
  }
  .holder__name {
    font-family: "Exo 2", sans-serif;
    font-weight: 600;
    font-size: 22px;
    line-height: 26px;
    margin: 0;
  }
  .holder__first { color: var(--brand-orange); }
  .holder__last { color: var(--brand-blue); }
  .holder__role {
    font-size: 16.5px;
    line-height: 20px;
    margin: 0;
  }
  .rule {
    width: 158px;
    height: 1px;
    background: var(--rule);
    margin: 0 auto;
    border: 0;
  }
  .rule--top { margin-top: 11px; }
  .contact {
    font-size: 16.5px;
    line-height: 21.5px;
    margin: 0;
  }
  .contact--phone { margin-top: 7px; }
  .rule--bottom { margin-top: 5px; }
  .contact--address { margin-top: 7px; }
</style>
</head>
<body>
<div class="canvas">
  <section class="card card--front">
    <svg class="brand-mark" viewBox="0 0 100 100" aria-hidden="true">
      <circle cx="50" cy="50" r="45" fill="none" stroke="var(--brand-orange)" stroke-width="7"/>
    </svg>
    <p class="brand-name">TALLOW PARTNERS</p>
    <div class="holder">
      <p class="holder__name"><span class="holder__first">DORIAN</span> <span class="holder__last">WHITLOCK</span></p>
      <p class="holder__role">Managing Director</p>
      <hr class="rule rule--top">
      <p class="contact contact--phone">(+244) 947 582 316<br>dorian.whitlock@tallow-p.example</p>
      <hr class="rule rule--bottom">
      <p class="contact contact--address">N ° 17/18 Rua Veloso - R / C<br>2B Direita<br>Bairro Mutamba - Luanda</p>
    </div>
  </section>
  <section class="card card--back">
    <p class="brand-name" style="text-align:center;">TALLOW PARTNERS</p>
  </section>
</div>
</body>
</html>
```